Permanent Makeup (cosmetics salon) Brochure

We need a 2-4 sites brochure for our Permanent Makeup (cosmetics salon). Our company is based in Austria / Vienna. -> Our homepage is www.ek-morgenstaller.at
This brochure should show which treatments we provide ot our customers.

I've uploaded our old brochure, the content (text) would be nearly the same (look form "Must Haves", pics have to be new (look uploaded pics)
The old brochure is to dark. -> look for our homepage maybe you can make it like this

Target Market(s)

woman, age 25-70 years who wants to have permanent makeup on eyebrows, lips or eyeliner

Industry/Entity Type

Beauty Salon

Requirements
Must have
• pics which are uploaded.

*This text (somithing about our business)
"Für Frau Morgenstaller ist Permanent Makeup ein Kunsthandwerk. Das Team von EK-Morgenstaller ist spezialisiert auf natürliches Permanent Makeup damit der individuelle Typ jeder Kundin am schönsten zum Ausdruck kommt."

*We do this treatments: (english)
+ Augenbrauen Microblading (eyebrows)
+ Augenbrauen Permanent Makeup (eyebrows2)
+ Lidstrich Permanent Makeup (eyeliner)
+ Lip Blushing (lips)
+ Lippen Permanent Makeup (lips2)

* Our addresses (2 locations)
Wien
Lindengasse 7b/12, 1010 Wien
Tel: 01/5827710

Villach
Birkenrainweg 4, 9524 St. Ulrich
Tel: 0676/3159082

Mail: info@ek-morgenstaller.at
www.ek-morgenstaller.at

```html
<!DOCTYPE html>
<html lang="de">
<head>
<meta charset="utf-8">
<title>EK-Morgenstaller Kosmetikstudio – Broschüre</title>
<link href="https://fonts.googleapis.com/css2?family=Bebas+Neue&family=Jost:wght@300;400;500&display=swap" rel="stylesheet">
<style>
  :root {
    --canvas: #eeeeee;
    --paper: #ffffff;
    --aqua: #2fe3ec;
    --aqua-soft: #bff6f8;
    --ink: #111111;
    --text: #3d3d3d;
    --muted: #7a7a7a;
    --skin-light: #ead2c2;
    --skin-mid: #c99e86;
    --room: #d9d6d3;
    --gold: #c9a24a;
  }
  * { box-sizing: border-box; margin: 0; padding: 0; }
  html, body { width: 1200px; height: 1200px; overflow: hidden; }
  body {
    background: var(--canvas);
    font-family: "Jost", "Helvetica Neue", sans-serif;
    color: var(--text);
    position: relative;
  }
  .page {
    position: absolute;
    width: 520px;
    height: 520px;
    background: var(--paper);
    overflow: hidden;
    box-shadow: 0 4px 16px rgba(0,0,0,.12);
  }
  .cover { left: 60px; top: 40px; }
  .back { left: 620px; top: 40px; }
  .spread {
    position: absolute;
    left: 80px; top: 620px;
    width: 1040px; height: 520px;
    box-shadow: 0 4px 16px rgba(0,0,0,.12);
  }
  .spread .page { box-shadow: none; top: 0; }
  .spread .inner-left { left: 0; }
  .spread .inner-right { left: 520px; border-left: 1px solid #eaeaea; }
  .shapes { position: absolute; inset: 0; width: 100%; height: 100%; }
  .photo { position: absolute; }
  .photo-portrait {
    left: 95px; top: 40px; width: 300px; height: 400px;
    background: linear-gradient(160deg, #5a4a44 0%, var(--skin-mid) 35%, var(--skin-light) 70%, #b8cfd4 100%);
  }
  .photo-shelf {
    left: 170px; top: 25px; width: 330px; height: 190px;
    background: linear-gradient(180deg, #cfcfcb 0%, #e3e2de 60%, #f2f1ee 100%);
  }
  .photo-room {
    left: 220px; top: 260px; width: 300px; height: 210px;
    background: linear-gradient(135deg, #e3dcdc 0%, var(--room) 55%, #efefef 100%);
  }
  .photo-eyes {
    left: 10px; top: 175px; width: 450px; height: 185px;
    background: linear-gradient(90deg, var(--skin-light) 0%, var(--skin-mid) 50%, #e7d4c8 100%);
  }
  .photo-lips {
    left: 40px; top: 180px; width: 360px; height: 260px;
    background: linear-gradient(180deg, var(--skin-mid) 0%, #e8a6a0 50%, var(--skin-light) 100%);
  }
  .z { position: absolute; z-index: 2; }
  .headline {
    font-family: "Bebas Neue", "Arial Narrow", sans-serif;
    color: var(--ink);
    letter-spacing: 3px;
    line-height: 1;
  }
  .cover-title { left: 210px; top: 340px; font-size: 62px; }
  .cover-sub {
    left: 175px; top: 405px;
    font-weight: 300; font-size: 21px; letter-spacing: .5px;
    color: var(--muted); text-transform: uppercase;
    border-bottom: 1px solid var(--muted); padding-bottom: 2px;
  }
  .brand {
    display: flex; align-items: center; gap: 8px;
    font-family: "Jost", sans-serif; font-weight: 400;
    font-size: 15px; color: var(--ink); letter-spacing: .5px;
  }
  .brand-dot {
    width: 18px; height: 18px; border-radius: 50%;
    border: 1.5px solid var(--gold);
  }
  .brand-tagline {
    font-size: 7px; letter-spacing: 1.5px; text-transform: uppercase;
    color: var(--ink); font-weight: 500; margin-top: 3px; text-align: center;
  }
  .cover-brand { left: 250px; top: 448px; }
  .contact {
    left: 24px; top: 225px; font-size: 13.5px; line-height: 1.35; color: var(--text);
  }
  .back-brand { left: 30px; top: 470px; }
  .kicker { font-size: 10px; letter-spacing: 2.5px; text-transform: uppercase; margin-top: 3px; text-align: center; color: var(--ink); font-weight: 500; }
  .intro-lead { left: 0; width: 520px; top: 40px; text-align: center; font-weight: 300; font-size: 20px; color: var(--muted); }
  .intro-einer { left: 0; width: 520px; top: 72px; text-align: center; font-style: italic; font-size: 13px; letter-spacing: 5px; color: var(--text); }
  .intro-title { left: 0; width: 520px; top: 92px; text-align: center; font-size: 52px; }
  .about { left: 30px; top: 380px; width: 400px; font-size: 12.5px; line-height: 1.4; }
  .left-brand { left: 230px; top: 470px; }
  .services { left: 30px; top: 30px; list-style: none; font-size: 12.5px; line-height: 1.25; color: var(--text); }
  .right-brand { left: 280px; top: 462px; }
</style>
</head>
<body>

<section class="page cover" aria-label="Titelseite">
  <div class="photo photo-portrait" role="img" aria-label="Porträtfoto einer Frau mit natürlichem Make-up"></div>
  <svg class="shapes" viewBox="0 0 520 520" preserveAspectRatio="none" aria-hidden="true">
    <defs>
      <linearGradient id="coverAqua" x1="0" y1="1" x2="0.3" y2="0">
        <stop offset="0" stop-color="#2fe3ec"/>
        <stop offset="1" stop-color="#ffffff" stop-opacity=".2"/>
      </linearGradient>
    </defs>
    <polygon points="395,120 520,250 520,520 0,520 0,330 170,400" fill="url(#coverAqua)" opacity=".85"/>
    <polygon points="300,520 520,420 520,520" fill="#ffffff"/>
  </svg>
  <h1 class="z headline cover-title">Schönheit</h1>
  <p class="z cover-sub">Kommt nicht nur von innen</p>
  <div class="z cover-brand">
    <div class="brand"><span class="brand-dot"></span>Elvira Morgenstaller</div>
    <div class="brand-tagline">Was Ihnen wertvoll ist, gehört in gute Hände</div>
  </div>
</section>

<section class="page back" aria-label="Rückseite">
  <svg class="shapes" viewBox="0 0 520 520" preserveAspectRatio="none" aria-hidden="true">
    <defs>
      <linearGradient id="backAqua" x1="0" y1="0" x2="1" y2="0.6">
        <stop offset="0" stop-color="#2fe3ec"/>
        <stop offset="1" stop-color="#ffffff"/>
      </linearGradient>
    </defs>
    <polygon points="0,150 200,260 520,470 520,520 0,520" fill="url(#backAqua)" opacity=".9"/>
    <polygon points="0,300 120,310 160,520 0,520" fill="#ffffff"/>
    <polygon points="470,520 520,470 520,520" fill="#ffffff"/>
  </svg>
  <div class="photo photo-shelf" role="img" aria-label="Foto einer Ablage mit Seifenspendern und Handtuchkorb"></div>
  <div class="photo photo-room" role="img" aria-label="Foto des Behandlungsraums mit Kosmetikerin"></div>
  <address class="z contact" style="font-style:normal">
    EK-Morgenstaller Kosmetikstudio<br>
    Ahornweg 5/8, 1010 Wien,<br>
    Österreich<br>
    Termine nur nach Vereinbarung<br>
    Tel: 0064/4918263<br>
    E-Mail: info@ek-morgenstaller.at<br>
    www.ek-morgenstaller.at
  </address>
  <div class="z back-brand">
    <div class="brand"><span class="brand-dot"></span>Elvira Morgenstaller</div>
    <div class="kicker">Kosmetikstudio</div>
  </div>
</section>

<div class="spread">
  <section class="page inner-left" aria-label="Innenseite links">
    <div class="photo photo-eyes" role="img" aria-label="Nahaufnahme von Augen und Augenbrauen"></div>
    <svg class="shapes" viewBox="0 0 520 520" preserveAspectRatio="none" aria-hidden="true">
      <defs>
        <linearGradient id="leftAqua" x1="1" y1="0" x2="0.2" y2="0.6">
          <stop offset="0" stop-color="#ffffff"/>
          <stop offset="1" stop-color="#2fe3ec"/>
        </linearGradient>
        <linearGradient id="leftCorner" x1="0" y1="1" x2="1" y2="0">
          <stop offset="0" stop-color="#2fe3ec"/>
          <stop offset="1" stop-color="#ffffff"/>
        </linearGradient>
      </defs>
      <polygon points="230,0 520,0 520,330 180,160" fill="url(#leftAqua)" opacity=".55"/>
      <polygon points="230,175 460,175 520,360 470,520 330,520 500,360" fill="url(#leftCorner)" opacity=".8"/>
    </svg>
    <p class="z intro-lead">Macht jeden Augenblik zu</p>
    <p class="z intro-einer">einer</p>
    <h2 class="z headline intro-title">Augenweide</h2>
    <p class="z about">Für Elvira Morgenstaller ist Kosmetik ein Kunsthandwerk. Und das gilt nicht nur für ihr Spezialgebiet Microblading. Das Team von EK-Morgenstaller bietet eine breite Palette hochwertiger kosmetischer Behandlungen und Anwendungen damit der individuelle Typ jeder Kundin am schönsten zum Ausdruck kommt.</p>
    <div class="z left-brand">
      <div class="brand"><span class="brand-dot"></span>Elvira Morgenstaller</div>
      <div class="kicker">Kosmetikstudio</div>
    </div>
  </section>

  <section class="page inner-right" aria-label="Innenseite rechts">
    <div class="photo photo-lips" role="img" aria-label="Nahaufnahme von Lippen mit natürlichem Permanent Make-up"></div>
    <svg class="shapes" viewBox="0 0 520 520" preserveAspectRatio="none" aria-hidden="true">
      <defs>
        <linearGradient id="rightAqua" x1="0.5" y1="0" x2="0.5" y2="1">
          <stop offset="0" stop-color="#2fe3ec"/>
          <stop offset="1" stop-color="#ffffff"/>
        </linearGradient>
      </defs>
      <polygon points="520,60 520,380 300,440 290,330" fill="url(#rightAqua)" opacity=".85"/>
      <polygon points="180,420 330,430 180,520 130,520" fill="#2fe3ec" opacity=".15"/>
      <polygon points="440,330 520,380 520,520 300,520" fill="#ffffff"/>
    </svg>
    <ul class="z services">
      <li>Microblading auf höchstem Niveau</li>
      <li>Permanent Make Up für Lippen</li>
      <li>Permanent Make Up als Lidstrich</li>
      <li>Wimpernverlängerung</li>
      <li>Gesichtbehandlungen</li>
      <li>Professionelles Make Up für Hochzeiten und alle Anlässe</li>
      <li>Sugaring / Haarentfernung</li>
      <li>...und vieles mehr</li>
    </ul>
    <div class="z right-brand">
      <div class="brand"><span class="brand-dot"></span>Elvira Morgenstaller</div>
      <div class="kicker">Kosmetikstudio</div>
    </div>
  </section>
</div>

</body>
</html>
```